We also do Plumbing Reminder! Our Primary Color is Green with Gold accent.

We are a HVAC, plumbing, and Controls contractor based out of West Michigan, Serving the entire west side of the state.
We want to remind our customers we do plumbing. Customers don't know or remember that we do plumbing. We would like the final design to show images, and descriptions of plumbing services we offer.

Lift Stations
Sinks
Confined Space
Backflow Prevention Devices​ (testing, installation, & service)
Drinking Fountains
Roof Drains
Sump Pumps
Water Main Emergency Service
Toilets / Urinals
Faucets / Shower Valves
Piping​ (copper, PVC, steel, PEX, galvanized)
Water Heaters
Floor and Sink Drains
​NEW INSTALLATIONS, SERVICE, AND MAINTENANCE OF ALL BRANDS OF EQUIPMENT

```html
<!DOCTYPE html>
<html lang="en">
<head>
<meta charset="utf-8">
<title>Lakeshore Mechanical – Plumbing Services Flyer</title>
<link rel="stylesheet" href="https://fonts.googleapis.com/css2?family=Poppins:wght@400;500;600;700&display=swap">
<style>
  :root{
    --green:#17754a;
    --green-dark:#0f5c39;
    --ink:#1f1f1f;
    --rule:#3a3a3a;
    --paper:#ffffff;
    --backdrop:#e9eaec;
  }
  *{box-sizing:border-box;margin:0;padding:0}
  html,body{width:1200px;height:2824px;overflow:hidden;background:var(--backdrop)}
  body{font-family:"Poppins",sans-serif;color:var(--ink);position:relative}
  .flyer{position:absolute;left:50px;top:702px;width:1100px;height:1419px;background:var(--paper);
    box-shadow:0 6px 22px rgba(0,0,0,.25);overflow:hidden}
  .hero{position:absolute;left:0;top:0;width:1100px;height:780px}
  .brand{position:absolute;left:80px;top:70px;width:340px;text-align:center;font-weight:700;color:var(--green);
    font-size:42px;line-height:1.05;letter-spacing:1px}
  .brand-mark{display:block;width:46px;height:46px;border-radius:50%;background:var(--green);margin:0 auto 12px}
  .intro{position:absolute;left:68px;top:760px;width:980px;font-size:24px;font-weight:500;line-height:43px}
  .intro strong{color:var(--green);font-weight:700;font-size:31px}
  .services{position:absolute;left:112px;top:944px;width:778px;height:364px;border:2px solid var(--green);border-radius:22px}
  .services-tab{position:absolute;left:315px;top:912px;width:425px;height:50px;background:var(--green);color:#fff;
    font-weight:700;font-size:30px;text-align:center;line-height:52px;letter-spacing:.5px}
  .service-list{position:absolute;left:148px;top:975px;width:760px;list-style:none;font-size:21px;font-weight:500;
    display:grid;grid-template-columns:364px 396px;row-gap:3px;line-height:32px}
  .service-list li{padding-left:18px;position:relative}
  .service-list li::before{content:"•";position:absolute;left:0}
  .service-list .wide{grid-column:1 / 3}
  .service-list .note{display:block;font-size:17px;font-weight:400;line-height:20px;margin-left:-6px;margin-bottom:8px}
  .service-list .caps{line-height:26px}
  .footer-rule{position:absolute;left:0;top:1338px;width:1100px;height:5px;background:var(--rule)}
  .footer{position:absolute;left:0;top:1350px;width:1100px;height:69px;background:var(--green);color:#fff;
    font-size:18px;font-weight:600}
  .footer-address{position:absolute;left:90px;top:14px;line-height:21px}
  .footer-phone{position:absolute;left:390px;top:22px;font-size:20px;display:flex;align-items:center;gap:14px}
  .footer-web{position:absolute;left:670px;top:6px;line-height:29px;font-size:20px}
  .footer-web span{display:flex;align-items:center;gap:14px}
  svg.icon{width:18px;height:18px;fill:#fff}
</style>
</head>
<body>
<main class="flyer">
  <svg class="hero" viewBox="0 0 1100 780" aria-hidden="false">
    <defs>
      <linearGradient id="sand" x1="0" y1="0" x2="1" y2="1">
        <stop offset="0" stop-color="#c9c3b6"/><stop offset=".5" stop-color="#a88e6c"/><stop offset="1" stop-color="#8d7657"/>
      </linearGradient>
      <linearGradient id="mech" x1="0" y1="0" x2="1" y2="0">
        <stop offset="0" stop-color="#8a8884"/><stop offset=".5" stop-color="#c7c6c2"/><stop offset="1" stop-color="#e4e4e2"/>
      </linearGradient>
      <linearGradient id="valve" x1="0" y1="0" x2="1" y2="1">
        <stop offset="0" stop-color="#b9a57a"/><stop offset="1" stop-color="#7c7a70"/>
      </linearGradient>
      <linearGradient id="fade" x1="0" y1="0" x2="0" y2="1">
        <stop offset="0" stop-color="#fff" stop-opacity="0"/><stop offset="1" stop-color="#fff"/>
      </linearGradient>
      <clipPath id="disc"><circle cx="713" cy="533" r="226"/></clipPath>
    </defs>
    <rect x="0" y="190" width="620" height="438" fill="url(#sand)" role="img" aria-label="Photo of a plumber fitting PVC drain pipe in an excavated trench"/>
    <rect x="0" y="628" width="640" height="8" fill="var(--green)"/>
    <path d="M600 0 H1100 V636 H600 Z" fill="url(#mech)" role="img" aria-label="Photo of commercial water heaters and piping in a mechanical room"/>
    <path d="M0 0 H680 C600 70 560 170 420 190 H0 Z" fill="#fff"/>
    <rect x="0" y="636" width="1100" height="150" fill="url(#fade)"/>
    <circle cx="713" cy="533" r="238" fill="#fff" stroke="var(--green)" stroke-width="2"/>
    <g clip-path="url(#disc)">
      <rect x="487" y="307" width="452" height="226" fill="url(#valve)" role="img" aria-label="Photo of backflow prevention valves"/>
      <rect x="487" y="533" width="226" height="226" fill="#a39c90" role="img" aria-label="Photo of a backflow device on a brick wall"/>
      <rect x="713" y="533" width="226" height="226" fill="#c9ccce" role="img" aria-label="Photo of restroom partitions and sinks"/>
      <rect x="600" y="600" width="226" height="160" fill="#e6e8ea" role="img" aria-label="Photo of a row of urinals"/>
      <path d="M487 307 L939 759 M939 307 L487 759" stroke="var(--green)" stroke-width="14"/>
    </g>
    <circle cx="713" cy="533" r="58" fill="#fff"/>
  </svg>

  <div class="brand"><span class="brand-mark"></span>LAKESHORE<br>MECHANICAL</div>

  <p class="intro">We are a <strong>HVAC, PLUMBING,</strong> and<br>Controls contractor based out of <strong>West Michigan,</strong> Serving the entire<br>west side of the state.</p>

  <div class="services"></div>
  <h2 class="services-tab">OUR SERVICES</h2>
  <ul class="service-list">
    <li>Lift Stations</li><li>Sinks</li>
    <li>Confined Space</li><li>Backflow Prevention Devices<span class="note">(testing, installation, &amp; service)</span></li>
    <li>Drinking Fountains</li><li>Roof Drains</li>
    <li>Sump Pumps</li><li>Water Main Emergency Service</li>
    <li>Toilets / Urinals</li><li>Faucets / Shower Valves</li>
    <li class="wide">Piping (copper, PVC, steel, PEX, galvanized)</li>
    <li>Water Heaters</li><li>Floor and Sink Drains</li>
    <li class="wide caps">NEW INSTALLATIONS, SERVICE, AND MAINTENANCE OF ALL BRANDS OF EQUIPMENT</li>
  </ul>

  <div class="footer-rule"></div>
  <footer class="footer">
    <div class="footer-address">1420 Maple Ridge Dr NE, Alpine,<br>MI, United States, Michigan</div>
    <div class="footer-phone">
      <svg class="icon" viewBox="0 0 24 24"><path d="M6.6 10.8a15.1 15.1 0 0 0 6.6 6.6l2.2-2.2c.3-.3.7-.4 1-.2 1.1.4 2.3.6 3.6.6.6 0 1 .4 1 1V20c0 .6-.4 1-1 1A17 17 0 0 1 3 4c0-.6.4-1 1-1h3.5c.6 0 1 .4 1 1 0 1.3.2 2.5.6 3.6.1.3 0 .7-.2 1z"/></svg>
      +1 616-555-0142
    </div>
    <div class="footer-web">
      <span><svg class="icon" viewBox="0 0 24 24"><path d="M2 5h20v14H2z M2 5l10 8 10-8" fill="none" stroke="#fff" stroke-width="2"/></svg>dana@lakeshoreind.com</span>
      <span><svg class="icon" viewBox="0 0 24 24"><circle cx="12" cy="12" r="9" fill="none" stroke="#fff" stroke-width="2"/><path d="M3 12h18M12 3c3 3 3 15 0 18M12 3c-3 3-3 15 0 18" fill="none" stroke="#fff" stroke-width="1.6"/></svg>lakeshoremechanical.com</span>
    </div>
  </footer>
</main>
</body>
</html>
```